New Banner Ad Design Project

We are a start-up in San Francisco that sells consignment clothes with a percentage of the proceeds donated to charity. Also, volunteer groups can conduct dress drives and send them to us and we will sell them and give their charity back 60% of the proceeds.

We have several uses for banners:
- Home page banner:
- Promote timely Flash Sales (they last only 96 hours) which happen 2x/week
- Promote how good it feels to give back and shop
- Promote any special promotions such as a Gift With Purchase
- Community banner:
- Promote the lifestyle
- Promote any particular group conducting a dress drive

If you are going to submit one banner it is to be for an upcoming sale, as the two attached files address (maternity sale). If we find the right designer we will consider working with them beyond the design contest for future sale banners as well as others

We consider our 'competitors' to be The Garment Venture, The TrueCloset, WeavTurn, KnitRise, WearAgain. Our key differentiator is the charitable components and how groups are conducting dress drives to raise money.

We are in the midst of changing our company name, tagline and logo. The new company will be called 'LunaTessa' and our tagline is 'Rewoven Kindness'

Target Market(s)

Our initial audience is young women 16 - 30. We will be focusing on Prom February through May which appeals to 16 - 18 year olds.

We also have maternity-wear. We want these women to feel fashionable

We are focused on individuals who want to give back.

Industry/Entity Type

Charity

Font styles to use
Serif
Sans Serif

Colors
8769ae
1b1b1b
474747
c3c3c3
86cfc6
b7a5cd

Requirements
Must have
• - Youthful and stylish voice (not to be confused with Young)
- Appealing visuals
- Powerful call-to-action as it pertains to banners for our flash sales
- An inclusive feel
- Communicates our charitable component
Nice to have
• - Emotional appeal
- Women wearing our clothes (see attached)
Should not have
• - Too much text
- Too girly; overly flowery

```html
<!DOCTYPE html>
<html lang="en">
<head>
<meta charset="utf-8">
<title>Maternity Sale Banner</title>
<link rel="stylesheet" href="https://fonts.googleapis.com/css2?family=Montserrat:wght@200;800&family=Raleway:wght@300&display=swap">
<style>
  :root {
    --teal: #86cfc6;
    --lilac: #b7a5cd;
    --white: #ffffff;
    --cream: #f6efe4;
    --skin: #e9c3ad;
    --blush: #d99a8c;
  }
  html, body {
    margin: 0;
    padding: 0;
    width: 1200px;
    height: 590px;
    overflow: hidden;
    background: var(--teal);
  }
  .banner {
    position: relative;
    width: 1200px;
    height: 590px;
    background: var(--teal);
  }
  .banner-art {
    display: block;
    width: 1200px;
    height: 590px;
  }
  .headline-kicker {
    font-family: "Montserrat", sans-serif;
    font-weight: 200;
    font-size: 143px;
    fill: var(--white);
  }
  .headline-main {
    font-family: "Montserrat", sans-serif;
    font-weight: 800;
    font-size: 340px;
  }
  .cta-badge { fill: var(--lilac); }
  .cta-label {
    font-family: "Raleway", sans-serif;
    font-weight: 300;
    font-size: 34px;
    fill: var(--white);
  }
  .cta-icon { fill: var(--white); }
  .cta-icon-handle {
    fill: none;
    stroke: var(--lilac);
    stroke-width: 2.5;
  }
</style>
</head>
<body>
<main class="banner">
  <svg class="banner-art" viewBox="0 0 1200 590" xmlns="http://www.w3.org/2000/svg">
    <defs>
      <linearGradient id="sale-photo-tones" x1="0" y1="0" x2="1" y2="0.3">
        <stop offset="0" stop-color="var(--cream)"/>
        <stop offset="0.28" stop-color="var(--skin)"/>
        <stop offset="0.5" stop-color="var(--blush)"/>
        <stop offset="0.72" stop-color="var(--cream)"/>
        <stop offset="1" stop-color="var(--cream)"/>
      </linearGradient>
    </defs>

    <text class="headline-kicker" x="40" y="198" textLength="805" lengthAdjust="spacingAndGlyphs">MATERNITY</text>

    <g role="img" aria-label="Lettering filled with a photo of a stylish woman in sunglasses and red lipstick">
      <text class="headline-main" x="38" y="472" fill="url(#sale-photo-tones)" textLength="800" lengthAdjust="spacingAndGlyphs">SALE</text>
    </g>

    <a href="#shop" class="cta">
      <circle class="cta-badge" cx="1020" cy="294" r="138"/>
      <text class="cta-label" x="1020" y="288" text-anchor="middle">SHOP NOW</text>
      <g class="cta-icon-bag">
        <path class="cta-icon" d="M994 318 L1046 318 L1048 378 L992 378 Z"/>
        <path class="cta-icon-handle" d="M1008 326 L1008 314 Q1008 302 1020 302 Q1032 302 1032 314 L1032 326"/>
        <path d="M1008 314 Q1008 302 1020 302 Q1032 302 1032 314" fill="none" stroke="var(--white)" stroke-width="2.5"/>
      </g>
    </a>
  </svg>
</main>
</body>
</html>
```